Craft Brewery Beer Can Label in Alaska

Design a 16oz can label for a craft brewery.

We are making a can design that can be used for our 6 normal beers. Our desire is to have a standard design but one major element have the color change on each beer type. We included examples of how this works for others.

Elements we general like in designs - mountain scenes, waterfalls, topo map lines, hops. None/all are not required in a design but gives starting options. We are on the ocean in a glacier fjord so think mountains, glaciers and water.

Requirements
Must have
• Company Logo – provided
Bellvane Seal Logo – provided
Saltmoor Brewers Logo – provided

Alcohol warning text -

GOVERNMENT WARNING: (1) According to the Surgeon General, women should not drink alcoholic beverages during pregnancy because of the risk of birth defects. (2) Consumption of alcoholic beverages impairs your ability to drive a car or operate machinery, and may cause health problems.

Beer Name – Gullrock Pilsner
ABV – 4.9% ABV
Size – 16 FL OZ
Nice to have
• Elements we general like in designs - mountain scenes, waterfalls, topo map lines, hops. None/all are not required in a design but gives starting options. We are on the ocean in a glacier fjord so think mountains, glaciers and water.

```html
<!DOCTYPE html>
<html lang="en">
<head>
<meta charset="utf-8">
<title>Gullrock Pilsner – Can Label</title>
<link rel="stylesheet" href="https://fonts.googleapis.com/css2?family=Bebas+Neue&family=Barlow:wght@500;600&display=swap">
<style>
  :root {
    --page: #f2f2f2;
    --gold: #e8bd2c;
    --gold-light: #eec93f;
    --amber: #e09a22;
    --rust: #a24a17;
    --oxblood: #4a1208;
    --ink: #553a10;
    --cream: #fdfbf2;
    --badge-dark: #3a3a3a;
    --badge-light: #ffffff;
    --display: "Bebas Neue", "Oswald", sans-serif;
    --text: "Barlow", "Helvetica Neue", sans-serif;
  }
  * { margin: 0; padding: 0; box-sizing: border-box; }
  html, body { width: 994px; height: 1200px; overflow: hidden; background: var(--page); }

  .label {
    position: absolute; left: 27px; top: 345px;
    width: 940px; height: 509px; overflow: hidden;
    background: linear-gradient(175deg, var(--gold-light) 0%, var(--gold) 45%);
    box-shadow: 0 2px 8px rgba(0,0,0,.12);
  }
  .landscape { position: absolute; left: 0; top: 0; width: 940px; height: 509px; }

  .front { position: absolute; top: 70px; width: 240px; text-align: center; }
  .front--left { left: 99px; }
  .front--right { left: 578px; }

  .brand-dot { display: block; width: 34px; height: 34px; border-radius: 50%; background: var(--ink); margin: 0 auto 8px; }
  .brand-name { font-family: var(--display); color: var(--ink); font-size: 34px; line-height: 28px; letter-spacing: .5px; }
  .brand-sub { font-family: var(--display); color: var(--ink); font-size: 12px; letter-spacing: 7px; line-height: 14px; padding-left: 7px; }

  .beer-name { margin-top: 24px; }
  .beer-name__style { display: block; font-family: var(--display); color: var(--ink); font-size: 48px; line-height: 40px; }
  .beer-name__type { display: block; font-family: var(--display); color: var(--cream); font-size: 64px; line-height: 54px; }

  .tagline {
    display: flex; align-items: center; gap: 6px; justify-content: center;
    font-family: var(--text); font-weight: 600; color: var(--ink);
    font-size: 8px; letter-spacing: 5px; margin-top: 10px;
  }
  .tagline::before, .tagline::after { content: ""; flex: 0 0 26px; height: 1.5px; background: var(--ink); }

  .spine-logo { position: absolute; left: 398px; top: 88px; width: 120px; text-align: center; }
  .spine-logo .brand-dot { width: 22px; height: 22px; margin-bottom: 6px; }
  .spine-logo .brand-name { font-size: 22px; line-height: 19px; }
  .spine-logo .brand-sub { font-size: 8px; letter-spacing: 4.5px; line-height: 10px; padding-left: 4px; }

  .spine { position: absolute; left: 348px; top: 238px; width: 220px; height: 100px; transform: rotate(-90deg); }
  .spine .beer-name { margin-top: 0; }
  .spine .beer-name__style { font-size: 44px; line-height: 36px; }
  .spine .beer-name__type { font-size: 58px; line-height: 48px; }
  .spine .tagline { justify-content: flex-start; margin-top: 6px; font-size: 7px; letter-spacing: 4.5px; }
  .spine .tagline::before { flex-basis: 8px; }

  .volume {
    position: absolute; top: 441px; width: 140px; text-align: center;
    font-family: var(--text); font-weight: 500; font-size: 8.5px; color: var(--gold-light); letter-spacing: .3px;
  }
  .volume--left { left: 149px; }
  .volume--right { left: 628px; }

  .warning {
    position: absolute; width: 270px;
    font-family: var(--text); font-weight: 500; font-size: 7px; line-height: 9px; color: #2a1a05;
    transform: rotate(-90deg); transform-origin: left top;
  }
  .warning strong { font-weight: 600; }
  .warning--left { left: 34px; top: 332px; }
  .warning--right { left: 864px; top: 318px; width: 245px; }

  .badge { position: absolute; }
  .badge--seal { left: 24px; top: 368px; width: 50px; height: 58px; background: var(--badge-light); border: 2px solid var(--badge-dark); }
  .badge--guild { left: 850px; top: 334px; width: 60px; height: 99px; background: var(--badge-dark); }
</style>
</head>
<body>
  <main class="label">
    <svg class="landscape" viewBox="0 0 940 509" role="img" aria-label="Layered mountain range fading from amber peaks to a dark fjord shoreline">
      <defs>
        <linearGradient id="range" x1="0" y1="0" x2="0" y2="1">
          <stop offset="0" stop-color="#e8bd2c" stop-opacity="0"/>
          <stop offset=".22" stop-color="#e09a22"/>
          <stop offset=".55" stop-color="#a24a17"/>
          <stop offset="1" stop-color="#4a1208"/>
        </linearGradient>
      </defs>
      <rect x="0" y="270" width="940" height="239" fill="url(#range)"/>
    </svg>

    <p class="warning warning--left"><strong>GOVERNMENT WARNING:</strong> (1) According to the Surgeon General, women should not drink alcoholic beverages during pregnancy because of the risk of birth defects.</p>
    <div class="badge badge--seal" aria-label="Bellvane Seal badge"></div>

    <section class="front front--left">
      <span class="brand-dot"></span>
      <div class="brand-name">HARROWPEAK</div>
      <div class="brand-sub">BREWING</div>
      <h1 class="beer-name">
        <span class="beer-name__style">GULLROCK</span>
        <span class="beer-name__type">PILSNER</span>
      </h1>
      <p class="tagline">CRAFT BREWERY</p>
    </section>
    <p class="volume volume--left">4.9% ABV &nbsp;|&nbsp; 16 FL OZ</p>

    <div class="spine-logo">
      <span class="brand-dot"></span>
      <div class="brand-name">HARROWPEAK</div>
      <div class="brand-sub">BREWING</div>
    </div>
    <div class="spine">
      <h2 class="beer-name">
        <span class="beer-name__style">GULLROCK</span>
        <span class="beer-name__type">PILSNER</span>
      </h2>
      <p class="tagline">CRAFT BREWERY</p>
    </div>

    <section class="front front--right">
      <span class="brand-dot"></span>
      <div class="brand-name">HARROWPEAK</div>
      <div class="brand-sub">BREWING</div>
      <h2 class="beer-name">
        <span class="beer-name__style">GULLROCK</span>
        <span class="beer-name__type">PILSNER</span>
      </h2>
      <p class="tagline">CRAFT BREWERY</p>
    </section>
    <p class="volume volume--right">4.9% ABV &nbsp;|&nbsp; 16 FL OZ</p>

    <p class="warning warning--right"><strong>GOVERNMENT WARNING:</strong> Consumption of alcoholic beverages impairs your ability to drive a car or operate machinery, and may cause health problems.</p>
    <div class="badge badge--guild" aria-label="Saltmoor Brewers badge"></div>
  </main>
</body>
</html>
```